SaaS Early tech startup business card design

Unique design for experience ecommerce platform company. the business cards will be used by executive members. conformance with color code is required.

```html
<!DOCTYPE html>
<html lang="en">
<head>
<meta charset="utf-8">
<title>Nuvora — Business Card</title>
<link rel="stylesheet" href="https://fonts.googleapis.com/css2?family=Montserrat:wght@500;700&family=Arimo:wght@400&display=swap">
<style>
  :root {
    --stage: #2b2b2d;
    --card-white: #ffffff;
    --blue-deep: #0b5e8c;
    --blue: #1386a8;
    --teal: #13a992;
    --teal-light: #3cbfa3;
    --ink: #1f1f1f;
    --rule: #d6d6d6;
  }
  * { margin: 0; padding: 0; box-sizing: border-box; }
  html, body { width: 1200px; height: 1015px; overflow: hidden; }
  body {
    background: var(--stage);
    font-family: "Arimo", Arial, sans-serif;
    position: relative;
  }
  .card {
    position: absolute;
    left: 320px;
    width: 560px;
    height: 320px;
    overflow: hidden;
    box-shadow: 0 10px 28px rgba(0,0,0,.55);
  }
  /* Back side */
  .card--back { top: 110px; }
  .back-band { position: absolute; left: 0; width: 100%; }
  .back-band--top {
    top: 0; height: 50%;
    background: linear-gradient(135deg, var(--blue-deep), var(--blue));
  }
  .back-band--bottom {
    bottom: 0; height: 50%;
    background: linear-gradient(135deg, var(--teal), var(--teal-light));
  }
  .back-wordmark {
    position: absolute; inset: 0;
    display: flex; align-items: center; justify-content: center;
    font-family: "Montserrat", Arial, sans-serif;
    font-weight: 700; font-size: 92px; letter-spacing: -2px;
    color: var(--card-white);
  }
  /* Front side */
  .card--front { top: 560px; background: var(--card-white); }
  .front-wordmark {
    position: absolute; left: 40px; top: 138px;
    font-family: "Montserrat", Arial, sans-serif;
    font-weight: 700; font-size: 64px; letter-spacing: -2px;
    color: var(--blue);
  }
  .divider {
    position: absolute; left: 300px; top: 30px; bottom: 30px;
    width: 1px; background: var(--rule);
  }
  .contact { position: absolute; left: 325px; top: 62px; }
  .contact__name {
    font-family: "Montserrat", Arial, sans-serif;
    font-weight: 500; font-size: 21px; color: var(--teal);
    letter-spacing: .3px;
  }
  .contact__role { font-size: 13.5px; color: var(--ink); margin-bottom: 16px; }
  .contact__line {
    display: flex; align-items: center; gap: 7px;
    font-size: 13px; color: var(--ink); line-height: 18px;
  }
  .contact__line svg { width: 12px; height: 12px; flex: none; }
  .contact__address {
    font-size: 13px; color: var(--ink); line-height: 17px;
    margin: 10px 0 0 19px;
  }
</style>
</head>
<body>
  <section class="card card--back" aria-label="Card back">
    <div class="back-band back-band--top" role="img" aria-label="Blue checkered pattern band"></div>
    <div class="back-band back-band--bottom" role="img" aria-label="Teal checkered pattern band"></div>
    <div class="back-wordmark">Nuvora</div>
  </section>

  <section class="card card--front" aria-label="Card front">
    <div class="front-wordmark">Nuvora</div>
    <div class="divider"></div>
    <div class="contact">
      <div class="contact__name">DANIEL REYES</div>
      <div class="contact__role">Managing Director</div>
      <div class="contact__line">
        <svg viewBox="0 0 24 24" aria-hidden="true"><path fill="var(--teal)" d="M6.6 10.8a15 15 0 0 0 6.6 6.6l2.2-2.2c.3-.3.7-.4 1-.2 1.1.4 2.3.6 3.6.6.6 0 1 .4 1 1V20c0 .6-.4 1-1 1A17 17 0 0 1 3 4c0-.6.4-1 1-1h3.5c.6 0 1 .4 1 1 0 1.3.2 2.5.6 3.6.1.3 0 .7-.2 1z"/></svg>
        044-987 654 321
      </div>
      <div class="contact__line">
        <svg viewBox="0 0 24 24" aria-hidden="true"><rect x="2" y="5" width="20" height="14" rx="1" fill="var(--blue)"/><path d="M2 6l10 7 10-7" fill="none" stroke="#fff" stroke-width="1.6"/></svg>
        hello@nuvora.com
      </div>
      <div class="contact__line">
        <svg viewBox="0 0 24 24" aria-hidden="true"><circle cx="12" cy="12" r="10" fill="none" stroke="var(--blue)" stroke-width="2"/><ellipse cx="12" cy="12" rx="4.5" ry="10" fill="none" stroke="var(--blue)" stroke-width="1.6"/><path d="M2 12h20M4 7h16M4 17h16" stroke="var(--blue)" stroke-width="1.4"/></svg>
        www.nuvora.com
      </div>
      <div class="contact__address">78, Harbour Lane West<br>30215, Eastland</div>
    </div>
  </section>
</body>
</html>
```